Aunt Roula's Bakery

I am about to create a luxury boutique that specializes in cake baking and cupcake
and ready for parties and special events and order delivery
the logo has already made

Boutique

Email:auntroulasbakery@mailbox-example.net
Instagram: aunt_roula_bakery
Twitter: xxxxxxx
WhatsApp: xxxxxxx

Requirements
Must have
• luxury design

```html
<!DOCTYPE html>
<html lang="en">
<head>
<meta charset="utf-8">
<title>Aunt Roula's Bakery – Business Card</title>
<link rel="stylesheet" href="https://fonts.googleapis.com/css2?family=Open+Sans:wght@400;700&display=swap">
<style>
  :root {
    --page-bg: #e9e6e2;
    --card-black: #0b0b0c;
    --card-sheen: #1c1c1f;
    --silver: #bdbdbd;
    --silver-soft: rgba(200, 200, 200, 0.28);
    --blush: #e8b9c6;
    --white: #f6f6f6;
  }
  html, body {
    margin: 0;
    width: 1200px;
    height: 1022px;
    overflow: hidden;
    background: var(--page-bg);
  }
  .business-card {
    position: absolute;
    left: 150px;
    top: 254px;
    width: 900px;
    height: 514px;
    border-radius: 6px;
    background: linear-gradient(135deg, var(--card-sheen) 0%, var(--card-black) 45%, var(--card-black) 100%);
    box-shadow: 0 18px 40px rgba(0, 0, 0, 0.35);
    overflow: hidden;
    font-family: "Open Sans", Arial, sans-serif;
  }
  .scroll-ornament {
    position: absolute;
    width: 300px;
    height: 150px;
  }
  .scroll-ornament--top-left {
    left: 0; top: 0;
    background: radial-gradient(ellipse at 0% 0%, var(--silver-soft) 0%, rgba(200,200,200,0.08) 55%, transparent 75%);
  }
  .scroll-ornament--top-right {
    right: 0; top: 0;
    background: radial-gradient(ellipse at 100% 0%, var(--silver-soft) 0%, rgba(200,200,200,0.08) 55%, transparent 75%);
  }
  .scroll-ornament--bottom-left {
    left: 0; bottom: 0;
    background: radial-gradient(ellipse at 0% 100%, var(--silver-soft) 0%, rgba(200,200,200,0.08) 55%, transparent 75%);
  }
  .scroll-ornament--bottom-right {
    right: 0; bottom: 0;
    background: radial-gradient(ellipse at 100% 100%, var(--silver-soft) 0%, rgba(200,200,200,0.08) 55%, transparent 75%);
  }
  .owner-block {
    position: absolute;
    left: 70px;
    top: 190px;
    text-align: right;
    width: 210px;
  }
  .owner-name {
    margin: 0;
    color: var(--white);
    font-weight: 700;
    font-size: 30px;
    letter-spacing: 0.5px;
  }
  .owner-title {
    margin: 2px 0 0;
    color: var(--blush);
    font-weight: 400;
    font-size: 16px;
    letter-spacing: 1px;
  }
  .brand-mark {
    position: absolute;
    left: 320px;
    top: 200px;
    width: 260px;
    display: flex;
    flex-direction: column;
    align-items: center;
    gap: 14px;
  }
  .brand-dot {
    width: 46px;
    height: 46px;
    border-radius: 50%;
    background: var(--blush);
  }
  .brand-name {
    margin: 0;
    color: var(--silver);
    font-weight: 400;
    font-size: 24px;
    letter-spacing: 2px;
    text-transform: uppercase;
    text-align: center;
  }
  .contact-list {
    position: absolute;
    left: 600px;
    top: 180px;
    margin: 0;
    padding: 0;
    list-style: none;
    color: var(--white);
    font-size: 16px;
    line-height: 1.75;
  }
  .contact-list .contact-label { font-weight: 400; }
  .contact-list .contact-value { color: var(--blush); }
  .contact-list .contact-value--email { font-size: 13.5px; }
</style>
</head>
<body>
  <section class="business-card" aria-label="Aunt Roula's Bakery business card">
    <div class="scroll-ornament scroll-ornament--top-left" role="img" aria-label="Silver scrollwork corner ornament"></div>
    <div class="scroll-ornament scroll-ornament--top-right" role="img" aria-label="Silver scrollwork corner ornament"></div>
    <div class="scroll-ornament scroll-ornament--bottom-left" role="img" aria-label="Silver scrollwork corner ornament"></div>
    <div class="scroll-ornament scroll-ornament--bottom-right" role="img" aria-label="Silver scrollwork corner ornament"></div>

    <div class="owner-block">
      <p class="owner-name">AUNT ROULA</p>
      <p class="owner-title">OWNER</p>
    </div>

    <div class="brand-mark">
      <div class="brand-dot"></div>
      <p class="brand-name">Aunt Roula's Bakery</p>
    </div>

    <ul class="contact-list">
      <li><span class="contact-label">Twitter:</span> <span class="contact-value">xxxxxxx</span></li>
      <li><span class="contact-label">WhatsApp:</span> <span class="contact-value">xxxxxxx</span></li>
      <li><span class="contact-label">Instagram:</span> <span class="contact-value">aunt_roula_bakery</span></li>
      <li><span class="contact-label">Email:</span> <span class="contact-value contact-value--email">auntroulasbakery@mailbox-example.net</span></li>
    </ul>
  </section>
</body>
</html>
```